Valdane Companies Business Card Design

We need a new business card for our Private Equity Real Estate Development firm, “Valdane” and our EB-5 regional center “Thornmere Regional Center” on one card. We prefer a design that is simple, elegant, and represents the luxury products we design and build as well as the financial security and stability our successful history has produced. We are an industry leader in our field and 3rd generation family business that has evolved into an institutional quality investment platform. Considered design size is standard business card dimensions (3.5 x 2 inches with an additional 1/8 inch space for design elements or backgrounds that extend beyond the finished size of your piece.

Target Market(s)

• High net worth individuals
• Highly skilled technical workers and physicians in the US seeking investment-based immigration opportunities
• Sophisticated private equity investors
• Intermediary partners include domestic attorneys and investment brokers, as well as international agent networks
• US real estate developers

Industry/Entity Type

Finance

Contact Information for Business Card

(Providing placeholder info for personal information, please design for longer character spaces, longer names and addresses etc..)
• Logo for Valdane
• Logo for Thornmere Regional Center
• Full name: Marcus Valdane
• Job title: CEO
• Email address: mvaldane@valdanecompanies.com
• Cell phone number: +1.555.314.2287
• Office number +1.555.628.4410
• Office address: Larkfield Court 5, 4817 Vista Orilla, Brindle Falls, OR.
• Website: www.valdanecompanies.com

Font styles to use
Serif
Sans Serif

Colors
ec1f27
ffffff
000000

Requirements
Must have
• • Logo for Valdane
• • Logo for Thornmere Regional Center
• - Use rounded corners
• (See .ai file included for logos)
Nice to have
• • Simple, elegant design
• • Aesthetically compatible with our website design (www.valdanecompanies.com)
• • Color palette including but not limited to white, black, and red (as per logos)
Should not have
• - Not too much red color
• - Do not stack both logos on top of each other

```html
<!DOCTYPE html>
<html lang="en">
<head>
<meta charset="utf-8">
<title>Valdane Companies Business Card</title>
<link rel="stylesheet" href="https://fonts.googleapis.com/css2?family=Montserrat:wght@400;500;600&display=swap">
<style>
  :root {
    --backdrop: #1f1f1f;
    --card: #262626;
    --white: #ffffff;
    --soft-white: #f2f2f2;
    --red: #a8182e;
  }
  * { margin: 0; padding: 0; box-sizing: border-box; }
  html, body {
    width: 1200px; height: 1200px; overflow: hidden;
    background: var(--backdrop);
    font-family: "Montserrat", sans-serif;
    color: var(--soft-white);
  }
  .card {
    position: absolute;
    left: 193px; width: 880px; height: 502px;
    background: var(--card);
    border-radius: 34px;
  }
  .card--front { top: 34px; }
  .card--back { top: 664px; }

  .brand {
    position: absolute;
    display: flex; align-items: center; gap: 16px;
    font-weight: 600;
    letter-spacing: 0.04em;
    white-space: nowrap;
  }
  .brand__mark { width: 44px; height: 44px; flex: none; }
  .brand--valdane { left: 40px; top: 66px; font-size: 44px; color: var(--white); }
  .brand--valdane .brand__mark { background: var(--white); }
  .brand--thornmere { right: 34px; bottom: 64px; font-size: 25px; color: var(--red); gap: 14px; }
  .brand--thornmere .brand__mark { background: var(--red); width: 34px; height: 34px; }

  .person { position: absolute; left: 40px; top: 190px; }
  .person__name { font-size: 35px; font-weight: 600; color: var(--white); line-height: 1.1; }
  .person__title { font-size: 21px; font-weight: 400; margin-top: 4px; }

  .address { position: absolute; left: 40px; top: 280px; font-size: 20.5px; line-height: 21px; font-style: normal; }

  .contacts { position: absolute; left: 40px; top: 343px; list-style: none; }
  .contacts li { display: flex; align-items: center; height: 28px; font-size: 19px; }
  .contacts svg { width: 18px; height: 18px; margin-right: 26px; fill: none; stroke: var(--soft-white); stroke-width: 1.6; }
</style>
</head>
<body>
  <section class="card card--front">
    <div class="brand brand--valdane"><span class="brand__mark"></span>Valdane Capital</div>

    <div class="person">
      <h1 class="person__name">Marcus Valdane</h1>
      <p class="person__title">CEO</p>
    </div>

    <address class="address">
      Larkfield Court 5, 4817<br>Vista Orilla Brindle Falls, OR
    </address>

    <ul class="contacts">
      <li><svg viewBox="0 0 18 18"><rect x="4.5" y="1" width="9" height="16" rx="1.5"/><line x1="8" y1="14.5" x2="10" y2="14.5"/></svg>+1555 - 314 - 2287</li>
      <li><svg viewBox="0 0 18 18"><path d="M2 7c0-3 14-3 14 0v1.5h-3.5V6.5h-7v2H2z" fill="#f2f2f2"/><rect x="4" y="9" width="10" height="6" rx="1" fill="#f2f2f2"/></svg>+1555 - 628 - 4410</li>
      <li><svg viewBox="0 0 18 18"><rect x="1.5" y="4" width="15" height="10"/><path d="M1.5 4l7.5 6 7.5-6M1.5 14l5.5-5M16.5 14l-5.5-5"/></svg>mvaldane@valdanecompanies.com</li>
      <li><svg viewBox="0 0 18 18"><circle cx="9" cy="9" r="7.5"/><ellipse cx="9" cy="9" rx="3.2" ry="7.5"/><line x1="1.5" y1="9" x2="16.5" y2="9"/><path d="M2.8 5h12.4M2.8 13h12.4"/></svg>www.valdanecompanies.com</li>
    </ul>
  </section>

  <section class="card card--back">
    <div class="brand brand--thornmere"><span class="brand__mark"></span>Thornmere Regional Center</div>
  </section>
</body>
</html>
```